The Wardrobe Sage needs a pricing flyer

Single page flyer for The Wardrobe Sage.
The Wardrobe Sage is a lead generation service exclusively for the custom closet industry.
You design quality closets we provide quality leads!
Value Points:
Leads for closet companies are exclusive with a first right of refusal. Meaning, if the closet company cannot handle all of the leads we can provide, we will sell the excess to other closet companies. We will never sell the same lead to two different closet companies.
Benefits:
Flat rate and easy to budget
Cancel at anytime
Choose from 3 types of leads
Lower cost compared to overall cost per lead from other sources
More leads allows hiring more designers
More leads grow the companies revenue
Less time managing other advertising models
3 service options.
$250 each
- We send you the lead
- You and your team set the appointment
- Setting the appointment is up to you
2. $275 each
- We send you the lead
- We guarantee the appointment
- Return unset appointments for a replacement
3. $375 each
- We are your call center
- We generate the lead
- We set the appointment
Contact:
The Wardrobe Sage
704-555-0183
leads@TheWardrobeSage.com

```html
<!DOCTYPE html>
<html lang="en">
<head>
<meta charset="UTF-8">
<title>The Wardrobe Sage – Pricing Flyer</title>
<link rel="stylesheet" href="https://fonts.googleapis.com/css2?family=Crimson+Text:wght@400;600&family=Didact+Gothic&display=swap">
<style>
  :root {
    --page-bg: #dfe2de;
    --paper: #ffffff;
    --charcoal: #2f2e33;
    --copper: #a0612a;
    --copper-card: #a2622d;
    --gold-text: #caa062;
    --ink: #222222;
    --body-gray: #555555;
    --card-ink: #2a1a0e;
    --service-bg-1: #4f5566;
    --service-bg-2: #8a8e98;
  }
  * { box-sizing: border-box; margin: 0; padding: 0; }
  html, body {
    width: 1200px; height: 900px; overflow: hidden;
    background: var(--page-bg);
  }
  .flyer {
    position: absolute; left: 321px; top: 20px;
    width: 557px; height: 860px;
    background: var(--paper);
    box-shadow: 0 4px 14px rgba(0,0,0,0.25);
    overflow: hidden;
    font-family: "Crimson Text", serif;
  }
  .hero { position: absolute; left: 0; top: 0; width: 557px; height: 370px; }
  .value-copy {
    position: absolute; right: 9px; top: 212px; width: 440px;
    text-align: right; color: var(--gold-text);
    font-size: 14px; line-height: 22.3px;
  }
  .benefits-title {
    position: absolute; left: 10px; top: 290px;
    color: var(--copper); font-size: 22px; font-weight: 600; letter-spacing: 0.5px;
  }
  .benefits-list {
    position: absolute; left: 10px; top: 327px; list-style: none;
    font-family: "Didact Gothic", sans-serif; color: var(--body-gray);
    font-size: 13.5px; line-height: 24.2px;
  }
  .service-title {
    position: absolute; left: 0; width: 557px; top: 451px; text-align: center;
    font-size: 18px; letter-spacing: 1.6px; color: var(--ink); font-weight: 600;
  }
  .service-band {
    position: absolute; left: 0; top: 484px; width: 557px; height: 251px;
    background: linear-gradient(120deg, var(--service-bg-2), var(--service-bg-1));
  }
  .plan {
    position: absolute; background: var(--copper-card);
    text-align: center; color: var(--card-ink);
    font-size: 14px; line-height: 24px;
    display: flex; flex-direction: column; justify-content: center;
  }
  .plan-price { color: #ffffff; font-size: 21px; font-weight: 600; margin-bottom: 6px; }
  .plan-item { margin-bottom: 5px; }
  .plan-basic { left: 7px; top: 8px; width: 164px; height: 234px; }
  .plan-guaranteed { left: 193px; top: 0; width: 177px; height: 242px; }
  .plan-callcenter { left: 392px; top: 8px; width: 165px; height: 234px; }
  .contact-title {
    position: absolute; left: 10px; top: 746px;
    color: var(--copper); font-size: 17px; font-weight: 600; letter-spacing: 1.8px;
  }
  .contact-name { position: absolute; left: 10px; top: 772px; font-size: 17px; color: var(--ink); letter-spacing: 0.5px; }
  .contact-phone { position: absolute; left: 10px; top: 792px; font-size: 24px; color: var(--ink); }
  .contact-email { position: absolute; left: 10px; top: 829px; font-size: 16px; color: var(--ink); letter-spacing: 0.4px; }
  .brand-mark {
    position: absolute; right: 14px; top: 800px;
    display: flex; align-items: center; gap: 8px;
    color: var(--copper); font-size: 26px; font-weight: 600;
  }
  .brand-dot { width: 14px; height: 14px; border-radius: 50%; background: var(--copper); }
</style>
</head>
<body>
  <main class="flyer">
    <svg class="hero" viewBox="0 0 557 370" aria-hidden="false">
      <defs>
        <linearGradient id="closet-tones" x1="0" y1="0" x2="1" y2="1">
          <stop offset="0" stop-color="#5a2e22"/>
          <stop offset="0.5" stop-color="#8a6a58"/>
          <stop offset="1" stop-color="#3b1f18"/>
        </linearGradient>
      </defs>
      <polygon role="img" aria-label="Luxury walk-in closet with dark wood shelving and a smiling woman standing in the centre"
               points="0,0 557,0 557,173 0,258" fill="url(#closet-tones)"/>
      <polygon points="0,258 557,173 557,363" fill="var(--charcoal)"/>
      <line x1="0" y1="258" x2="557" y2="173" stroke="var(--copper)" stroke-width="2"/>
      <line x1="0" y1="258" x2="557" y2="363" stroke="var(--copper)" stroke-width="3"/>
    </svg>

    <p class="value-copy">Leads for closet companies are exclusive with a first right of refusal. Meaning, if the closet company cannot handle all of the leads we can provide, we will sell the excess to other closet companies. We will never sell the same lead to two different closet companies.</p>

    <h2 class="benefits-title">BENEFITS -</h2>
    <ul class="benefits-list">
      <li>Flat rate and easy to budget</li>
      <li>Cancel at anytime | Choose from 3 types of leads</li>
      <li>Lower cost compared to overall cost per lead from other sources</li>
      <li>More leads allows hiring more designers | More leads grow the companies revenue</li>
      <li>Less time managing other advertising models</li>
    </ul>

    <h2 class="service-title">SERVICE OPTIONS</h2>

    <section class="service-band" role="img" aria-label="Blue-grey custom cabinetry interior behind the pricing cards">
      <div class="plan plan-basic">
        <div class="plan-price">$250 Each</div>
        <div class="plan-item">✓We send you the lead</div>
        <div class="plan-item">✓You and your team set<br>the appointment</div>
        <div class="plan-item">✓Setting the appointment<br>is up to you</div>
      </div>
      <div class="plan plan-guaranteed">
        <div class="plan-price">$275 Each</div>
        <div class="plan-item">✓We send you the lead</div>
        <div class="plan-item">✓You and your team set<br>the appointment</div>
        <div class="plan-item">✓We guarantee<br>the appointment</div>
        <div class="plan-item">✓Return unset appointments<br>for a replacement</div>
      </div>
      <div class="plan plan-callcenter">
        <div class="plan-price">$375 Each</div>
        <div class="plan-item">✓We are your call center</div>
        <div class="plan-item">✓We generate the lead</div>
        <div class="plan-item">✓We set the appointment</div>
      </div>
    </section>

    <h2 class="contact-title">CONTACT&nbsp; DETAILS</h2>
    <p class="contact-name">The Wardrobe Sage</p>
    <p class="contact-phone">704-555-0183</p>
    <p class="contact-email">leads@TheWardrobeSage.com</p>

    <div class="brand-mark"><span class="brand-dot"></span>Wardrobe Sage</div>
  </main>
</body>
</html>
```